Brightfield Ventures Inc. Letterhead

Creation of attractive and eye catching letterhead for a business start-up for the construction industry. Letterhead must relate to construction, but avoid standard hammer and tools in the design.

I forgot to add some details, sorry about that. Some pertinent info: Ph: 916-555-0187 brightfieldventures.example 448 Willowmere Ave, Ste 210 Folsom, CA 95999 info@brightfieldventures.example not sure if slogan should be in there" “Connecting construction professionals to create a purpose driven industry.” must be able to be used in word. Thanks!

```html
<!DOCTYPE html>
<html lang="en">
<head>
<meta charset="utf-8">
<title>Brightfield Ventures Inc. Letterhead</title>
<link rel="stylesheet" href="https://fonts.googleapis.com/css2?family=Source+Sans+3:wght@400;600&family=Arimo:wght@700&display=swap">
<style>
  :root {
    --backdrop: #e9e9e9;
    --paper: #ffffff;
    --brand-red: #b30d14;
    --brand-wine: #6b1230;
    --brand-navy: #131a4f;
    --ink: #2a2a2a;
    --body-ink: #555555;
    --contact-ink: #ffffff;
  }
  * { box-sizing: border-box; margin: 0; padding: 0; }
  html, body {
    width: 1200px; height: 1200px; overflow: hidden;
    background: var(--backdrop);
  }
  .letterhead {
    position: absolute; left: 203px; top: 40px;
    width: 794px; height: 1120px;
    background: var(--paper);
    overflow: hidden;
    font-family: "Source Sans 3", sans-serif;
  }
  .header-band {
    position: absolute; left: 0; top: 0; width: 100%; height: 140px;
    background: linear-gradient(90deg, var(--brand-red) 0%, var(--brand-wine) 45%, var(--brand-navy) 100%);
  }
  .brand {
    position: absolute; left: 75px; top: 168px;
    display: flex; align-items: center; gap: 10px;
  }
  .brand-mark { width: 16px; height: 16px; background: var(--brand-red); flex: none; }
  .brand-name {
    font-weight: 600; font-size: 21px; letter-spacing: 1.5px;
    text-transform: uppercase; color: var(--brand-navy); line-height: 1.1;
  }
  .contact {
    position: absolute; left: 580px; top: 22px;
    color: var(--contact-ink); font-size: 11px; line-height: 16px;
  }
  .contact li { list-style: none; display: flex; align-items: center; gap: 5px; }
  .contact svg { width: 9px; height: 9px; fill: var(--contact-ink); flex: none; }
  .contact address { font-style: normal; margin-top: 8px; }
  .greeting {
    position: absolute; left: 75px; top: 275px;
    font-family: "Arimo", sans-serif; font-weight: 700; font-size: 17px; color: var(--ink);
  }
  .letter-body { position: absolute; left: 75px; top: 319px; width: 644px; }
  .letter-body p {
    font-size: 17.2px; line-height: 20.8px; color: var(--body-ink);
    text-align: justify; margin-bottom: 20.8px;
  }
  .signature {
    position: absolute; left: 75px; top: 880px; width: 125px; height: 60px;
    background: linear-gradient(90deg, #f2f2f2, #e6e6e6);
  }
  .footer-band {
    position: absolute; left: 0; bottom: 0; width: 100%; height: 12px;
    background: var(--brand-red);
  }
</style>
</head>
<body>
<main class="letterhead">
  <div class="header-band" role="img" aria-label="Decorative header area in red to navy brand tones"></div>

  <div class="brand">
    <span class="brand-mark"></span>
    <span class="brand-name">Brightfield Ventures</span>
  </div>

  <ul class="contact">
    <li><svg viewBox="0 0 10 10"><path d="M2 0 L4 2.5 L3 3.6 C3.8 5.2 4.8 6.2 6.4 7 L7.5 6 L10 8 L8.6 10 C4 9.5 0.5 6 0 1.4 Z"/></svg>916-555-0187</li>
    <li><svg viewBox="0 0 10 10"><path d="M0 2 H10 V8 H0 Z M0.6 2.4 L5 5.6 L9.4 2.4" stroke="#131a4f" stroke-width="0.8"/></svg>info@brightfieldventures.example</li>
    <li><svg viewBox="0 0 10 10"><circle cx="5" cy="5" r="4.5"/><path d="M0.5 5 H9.5 M5 0.5 V9.5" stroke="#131a4f" stroke-width="0.7"/></svg>brightfieldventures.example</li>
    <li><address>448 Willowmere Ave, Ste 210,<br>Folsom, CA 95999</address></li>
  </ul>

  <h1 class="greeting">Dear Mr. Harlow,</h1>

  <section class="letter-body">
    <p>Lorem Ipsum is simply dummy text of the printing and typesetting industry. Lorem Ipsum has been the industry's standard dummy text ever since the 1500s, when an unknown printer took a galley of type and scrambled it to make a type specimen book. It has survived not only five centuries, but also the leap into electronic typesetting, remaining essentially unchanged.</p>
    <p>The standard chunk of Lorem Ipsum used since the 1500s is reproduced below for those interested. Sections 1.10.32 and 1.10.33 from "de Finibus Bonorum et Malorum" by Cicero are also reproduced in their exact original form, accompanied by English versions from the 1914 translation by H. Rackham</p>
    <p>Lorem Ipsum is simply dummy text of the printing and typesetting industry. Lorem Ipsum has been the industry's standard dummy text ever since the 1500s, when an unknown printer took a galley of type and scrambled it to make a type specimen book. It has survived not only five centuries, but also the leap into electronic typesetting, remaining essentially unchanged. It was popularised in the</p>
    <p>The standard chunk of Lorem Ipsum used since the 1500s is reproduced below for those interested. Sections 1.10.32 and 1.10.33 from "de Finibus Bonorum et Malorum" by Cicero are also reproduced in their exact original form, accompanied by English versions from the 1914 translation by H. Rackham</p>
    <p>The standard chunk of Lorem Ipsum used since the 1500s is reproduced below for those interested. Sections 1.10.32 and 1.10.33 from "de Finibus Bonorum et Malorum" by Cicero</p>
  </section>

  <div class="signature" role="img" aria-label="Handwritten signature of the sender"></div>

  <div class="footer-band"></div>
</main>
</body>
</html>
```